CBD AgriBusiness Verdant Trophy Business Card

We are HiTec producer of medical cannabis CBD Switzerland of high quality. Our website is alpinleaf.net, we will also revisit it graphically, the winner of this contest will be the graphic designer chosen for the new design of the website. We stand out by the skill of the team, many of our engineers we win cup cannabis. I join the current map to take as an example but to revisit completely: deletion of surname and first name, modification of funds (front / back), reorganization of text info, highlighting the address of the website. three characteristics define the business card: Professional, Class, refined. The business card must be optimized for soft-touch and selective varnish printing.

Target Market(s)

Customers and Suppliers

Industry/Entity Type

Agribusiness

Contact Information for Business Card

Logo, Tél / Whatsapp, mail, url du site : alpinleaf.net

Font styles to use
Sans Serif

Requirements
Must have
• Logo of alpinleaf.net
Nice to have
• a design that stands out well on the selective varnish
Should not have
• Last name and first name

```html
<!DOCTYPE html>
<html lang="en">
<head>
<meta charset="utf-8">
<title>alpinleaf business card</title>
<link href="https://fonts.googleapis.com/css2?family=Work+Sans:wght@400;600;800&display=swap" rel="stylesheet">
<style>
  :root {
    --backdrop: #b9b9b9;
    --leaf-green: #9cca6a;
    --ink-grey: #4a4a4a;
    --text-grey: #555555;
    --card-white: #ffffff;
  }
  html, body {
    margin: 0;
    padding: 0;
    overflow: hidden;
  }
  .canvas {
    position: relative;
    width: 1200px;
    height: 930px;
    background: var(--backdrop);
    font-family: "Work Sans", Arial, sans-serif;
    overflow: hidden;
  }
  .card {
    position: absolute;
    width: 560px;
    height: 320px;
    border-radius: 26px;
    box-shadow: 0 6px 18px rgba(0, 0, 0, 0.18);
    box-sizing: border-box;
  }
  .card--front {
    left: 110px;
    top: 90px;
    background: var(--leaf-green);
    display: flex;
    align-items: center;
    justify-content: center;
  }
  .card--back {
    left: 530px;
    top: 510px;
    background: var(--card-white);
  }
  .brand {
    display: flex;
    align-items: center;
    gap: 12px;
    font-weight: 800;
    letter-spacing: -1px;
  }
  .brand__square {
    display: block;
    flex: none;
  }
  .brand--front {
    color: var(--card-white);
    font-size: 62px;
  }
  .brand--front .brand__square {
    width: 34px;
    height: 34px;
    background: var(--card-white);
  }
  .brand--back {
    position: absolute;
    left: 40px;
    top: 160px;
    color: var(--ink-grey);
    font-size: 44px;
  }
  .brand--back .brand__square {
    width: 24px;
    height: 24px;
    background: var(--leaf-green);
  }
  .divider {
    position: absolute;
    left: 300px;
    top: 50px;
    width: 2px;
    height: 200px;
    background: var(--leaf-green);
  }
  .contact {
    position: absolute;
    left: 322px;
    top: 66px;
    color: var(--text-grey);
    font-size: 13.5px;
    line-height: 1.45;
  }
  .contact__role {
    color: var(--leaf-green);
    font-weight: 600;
    font-size: 18px;
    letter-spacing: 0.5px;
    margin: 0 0 12px;
  }
  .contact__address {
    margin: 0 0 12px;
    font-style: normal;
  }
  .contact__list {
    list-style: none;
    margin: 0;
    padding: 0;
  }
  .contact__item {
    display: flex;
    align-items: center;
    gap: 8px;
  }
  .contact__icon {
    width: 11px;
    height: 11px;
    flex: none;
  }
  .contact__web-highlight {
    color: var(--leaf-green);
    font-weight: 600;
  }
</style>
</head>
<body>
<div class="canvas">
  <section class="card card--front">
    <div class="brand brand--front">
      <span class="brand__square"></span>
      <span class="brand__name">alpinleaf</span>
    </div>
  </section>

  <section class="card card--back">
    <div class="brand brand--back">
      <span class="brand__square"></span>
      <span class="brand__name">alpinleaf</span>
    </div>
    <div class="divider"></div>
    <div class="contact">
      <p class="contact__role">DIRECTOR</p>
      <address class="contact__address">42 Meadow Lane,<br>Lakeside, NZ, 8020</address>
      <ul class="contact__list">
        <li class="contact__item">
          <svg class="contact__icon" viewBox="0 0 12 12"><path d="M2 1l2 0 1 3-1.5 1a6 6 0 0 0 3.5 3.5L8 7l3 1 0 2c0 1-1 1-1 1A9 9 0 0 1 1 2s0-1 1-1z" fill="#9cca6a"/></svg>
          <span>+41 (0) 79 000 12 34</span>
        </li>
        <li class="contact__item">
          <svg class="contact__icon" viewBox="0 0 12 12"><rect x="3" y="0.5" width="6" height="11" rx="1" fill="none" stroke="#9cca6a" stroke-width="1.2"/><circle cx="6" cy="9.5" r="0.7" fill="#9cca6a"/></svg>
          <span>+44 7700 90 12 34</span>
        </li>
        <li class="contact__item">
          <svg class="contact__icon" viewBox="0 0 12 12"><rect x="0.6" y="2.5" width="10.8" height="7" fill="none" stroke="#9cca6a" stroke-width="1.2"/><path d="M0.6 2.5L6 6.5 11.4 2.5" fill="none" stroke="#9cca6a" stroke-width="1.2"/></svg>
          <span>office@alpinleaf.net</span>
        </li>
        <li class="contact__item">
          <svg class="contact__icon" viewBox="0 0 12 12"><circle cx="6" cy="6" r="5.2" fill="none" stroke="#9cca6a" stroke-width="1.2"/><path d="M0.8 6h10.4M6 0.8c-2.5 3-2.5 7.4 0 10.4M6 0.8c2.5 3 2.5 7.4 0 10.4" fill="none" stroke="#9cca6a" stroke-width="1"/></svg>
          <span>www.<span class="contact__web-highlight">alpinleaf</span>.net</span>
        </li>
      </ul>
    </div>
  </section>
</div>
</body>
</html>
```